Modern Business Card

Modern professional business card with more than just logo and demographic info. Something memorable.

We are a trendy/modern chiropractic group with an emphasis on neurology, hence the minimalist-type brain logo. We want to convey that modern and technical aspect with professionalism and the elite nature of our practice environment.

```html
<!DOCTYPE html>
<html lang="en">
<head>
<meta charset="utf-8">
<title>Kestrel Spine – Business Card</title>
<link rel="stylesheet" href="https://fonts.googleapis.com/css2?family=Libre+Baskerville:wght@400&family=Ubuntu:wght@500&family=Alegreya+Sans:wght@400&display=swap">
<style>
  :root {
    --backdrop: #3b3b3d;
    --card: #1d1d1f;
    --ink-light: #f2f2f2;
    --ink-muted: #d6d6d6;
    --accent: #4a6fb0;
    --emboss: #8a8a8c;
  }
  * { margin: 0; padding: 0; box-sizing: border-box; }
  html, body { width: 799px; height: 1200px; overflow: hidden; }
  body {
    background: var(--backdrop);
    display: flex;
    flex-direction: column;
    align-items: center;
    justify-content: space-around;
    font-family: "Alegreya Sans", sans-serif;
  }
  .card {
    position: relative;
    width: 580px;
    height: 330px;
    background: var(--card);
    border-radius: 6px;
    box-shadow: 0 14px 30px rgba(0,0,0,.45);
    overflow: hidden;
  }
  .card-front {
    display: flex;
    align-items: center;
    justify-content: center;
    gap: 16px;
  }
  .brand-dot {
    width: 22px; height: 22px;
    border-radius: 50%;
    background: var(--emboss);
  }
  .front-name {
    font-family: "Libre Baskerville", serif;
    font-size: 34px;
    letter-spacing: 3px;
    color: var(--emboss);
    text-transform: uppercase;
  }
  .wordmark {
    position: absolute;
    left: 44px; top: 36px;
    font-family: "Libre Baskerville", serif;
    color: var(--ink-light);
    text-transform: uppercase;
    line-height: 1;
  }
  .wordmark .line-1 { font-size: 34px; letter-spacing: 1px; display: block; }
  .wordmark .line-2 { font-size: 19px; letter-spacing: 2px; display: block; margin-top: 2px; }
  .person { position: absolute; left: 44px; top: 122px; }
  .person-name {
    font-family: "Ubuntu", sans-serif;
    font-weight: 500;
    font-size: 20px;
    color: var(--accent);
  }
  .person-role { font-size: 15px; color: var(--ink-muted); margin-top: 2px; }
  .contact { position: absolute; left: 44px; top: 188px; list-style: none; }
  .contact li {
    display: flex; align-items: center; gap: 10px;
    font-size: 15px; color: var(--ink-light);
    height: 22px;
  }
  .contact svg { width: 13px; height: 13px; fill: var(--accent); flex: none; }
  .contact .address { padding-left: 0; }
  .back-mark {
    position: absolute;
    right: 34px; bottom: 40px;
    display: flex; align-items: center; gap: 12px;
  }
  .back-mark .brand-dot { width: 40px; height: 40px; background: var(--accent); }
  .back-mark-text {
    font-family: "Libre Baskerville", serif;
    font-size: 30px;
    color: var(--accent);
    text-transform: uppercase;
    letter-spacing: 2px;
  }
</style>
</head>
<body>
  <section class="card card-front">
    <span class="brand-dot"></span>
    <span class="front-name">Kestrel Spine</span>
  </section>

  <section class="card card-back">
    <h1 class="wordmark"><span class="line-1">Kestrel</span><span class="line-2">Spine</span></h1>
    <div class="person">
      <p class="person-name">Alex Moreno</p>
      <p class="person-role">Managing Director</p>
    </div>
    <ul class="contact">
      <li><svg viewBox="0 0 16 16"><path d="M3 1l3 3-2 2c1 2 3 4 5 5l2-2 3 3-2 2C7 14 2 9 1 3z"/></svg>555-010-2040</li>
      <li><svg viewBox="0 0 16 16"><path d="M1 3h14v10H1z M1 3l7 6 7-6" stroke="#1d1d1f" stroke-width="1"/></svg>alex@kestrelspine.com</li>
      <li><svg viewBox="0 0 16 16"><circle cx="8" cy="8" r="7"/><path d="M1 8h14M8 1v14M3 4h10M3 12h10" stroke="#1d1d1f" stroke-width="1" fill="none"/></svg>www.kestrelspine.com</li>
      <li class="address">18 Harbor Lane, Millbrook,</li>
      <li class="address">Eastvale, US 40210</li>
    </ul>
    <div class="back-mark">
      <span class="brand-dot"></span>
      <span class="back-mark-text">Kestrel</span>
    </div>
  </section>
</body>
</html>
```